Verodex business card

Business card for sustainable investment company called "Verodex". Verodex is an exchange platform selling carbon credits between buyers and sellers. Carbon Credits are an environmental commodity for reducing global carbon emissions.

the card should obviously have our logo and the theme should be sustainability/environment mixed with a trading platform.

Contact Information for Business Card

Logo, Name, Title, Phone, Email

Colors
0054AA
0677BA
7BADD7
CADEEF
E8F1F8
0094D4
00A9DD
6FCCEA
C7EBF8
E9F6FB
00AB8E
00BBA5
67D7C9
C6EFE9
E9F9F6
59FF00
82FF00
B8FF75
E3FFCB
F4FFEA

```html
<!DOCTYPE html>
<html lang="en">
<head>
<meta charset="utf-8">
<title>Verodex Business Card</title>
<link href="https://fonts.googleapis.com/css2?family=Poppins:wght@400;500;600&display=swap" rel="stylesheet">
<style>
  :root {
    --stage: #1b1c1f;
    --card: #22324d;
    --card-edge: #1d2b43;
    --white: #ffffff;
    --cyan: #2ee0f2;
    --blue: #1f7af0;
    --rule: #6a7891;
    --pattern-dark: #141d2e;
    --pattern-light: #3a63a8;
  }
  * { box-sizing: border-box; margin: 0; padding: 0; }
  html, body { width: 1200px; height: 1108px; overflow: hidden; }
  body {
    background: var(--stage);
    font-family: "Poppins", sans-serif;
    position: relative;
  }
  .card {
    position: absolute;
    top: 234px;
    width: 400px;
    height: 640px;
    border-radius: 22px;
    background: var(--card);
    box-shadow: 0 18px 40px rgba(0,0,0,0.45);
    overflow: hidden;
  }
  .card--front { left: 150px; }
  .card--back { left: 650px; }

  .brand {
    position: absolute;
    top: 110px;
    left: 0; right: 0;
    display: flex;
    align-items: center;
    justify-content: center;
    gap: 14px;
  }
  .brand__square {
    width: 34px; height: 34px;
    border-radius: 6px;
    background: var(--cyan);
  }
  .brand__name {
    color: var(--white);
    font-weight: 600;
    font-size: 40px;
    letter-spacing: 1px;
    text-transform: uppercase;
  }

  .person {
    position: absolute;
    top: 398px;
    left: 0; right: 0;
    text-align: center;
  }
  .person__name {
    font-weight: 600;
    font-size: 29px;
    letter-spacing: 1px;
    text-transform: uppercase;
    background: linear-gradient(90deg, var(--cyan), var(--blue));
    -webkit-background-clip: text;
    background-clip: text;
    color: transparent;
    line-height: 1.1;
  }
  .person__title {
    color: var(--white);
    font-size: 15px;
    letter-spacing: 0.5px;
    text-transform: uppercase;
    margin-top: 2px;
  }

  .contact-icons {
    position: absolute;
    top: 478px;
    left: 40px; right: 40px;
    display: flex;
    align-items: center;
    gap: 8px;
  }
  .contact-icons__rule { flex: 1; height: 1px; background: var(--rule); }
  .contact-icon {
    width: 30px; height: 30px;
    border-radius: 5px;
    background: linear-gradient(135deg, var(--cyan), var(--blue));
    display: flex; align-items: center; justify-content: center;
  }

  .contact-list {
    position: absolute;
    top: 525px;
    left: 0; right: 0;
    list-style: none;
    text-align: center;
    color: var(--white);
    font-size: 17px;
    line-height: 1.45;
  }

  .back-pattern {
    position: absolute;
    inset: 0;
    background: linear-gradient(215deg, var(--pattern-light) 0%, #2a4370 35%, var(--card) 60%, var(--pattern-dark) 100%);
  }
  .back-mark {
    position: absolute;
    top: 440px;
    left: 210px;
    display: flex;
    align-items: center;
    gap: 8px;
  }
  .back-mark__square {
    width: 18px; height: 18px;
    border-radius: 4px;
    background: var(--cyan);
  }
  .back-mark__name {
    color: var(--cyan);
    font-weight: 600;
    font-size: 20px;
    text-transform: uppercase;
    letter-spacing: 1px;
  }
</style>
</head>
<body>
  <section class="card card--front">
    <div class="brand">
      <span class="brand__square"></span>
      <span class="brand__name">Verodex</span>
    </div>

    <div class="person">
      <p class="person__name">Marcus Hale</p>
      <p class="person__title">Managing Director</p>
    </div>

    <div class="contact-icons">
      <span class="contact-icons__rule"></span>
      <span class="contact-icon" aria-label="Phone">
        <svg width="18" height="18" viewBox="0 0 24 24"><path d="M6.6 10.8a15 15 0 0 0 6.6 6.6l2.2-2.2c.3-.3.7-.4 1-.2 1.1.4 2.3.6 3.6.6.6 0 1 .4 1 1V20c0 .6-.4 1-1 1A17 17 0 0 1 3 4c0-.6.4-1 1-1h3.5c.6 0 1 .4 1 1 0 1.3.2 2.5.6 3.6.1.3 0 .7-.2 1z" fill="#ffffff"/></svg>
      </span>
      <span class="contact-icon" aria-label="Email">
        <svg width="18" height="18" viewBox="0 0 24 24"><rect x="3" y="6" width="18" height="12" rx="1.5" fill="none" stroke="#ffffff" stroke-width="2"/><path d="M3 7l9 6 9-6" fill="none" stroke="#ffffff" stroke-width="2"/></svg>
      </span>
      <span class="contact-icon" aria-label="Website">
        <svg width="18" height="18" viewBox="0 0 24 24"><circle cx="12" cy="12" r="9" fill="none" stroke="#ffffff" stroke-width="2"/><path d="M3 12h18M12 3c3 3 3 15 0 18M12 3c-3 3-3 15 0 18" fill="none" stroke="#ffffff" stroke-width="1.5"/></svg>
      </span>
      <span class="contact-icons__rule"></span>
    </div>

    <ul class="contact-list">
      <li>044-987 654 321</li>
      <li>hello@verodexmail.com</li>
      <li>www.verodexhub.com</li>
    </ul>
  </section>

  <section class="card card--back">
    <div class="back-pattern" role="img" aria-label="Repeating embossed brand pattern fading from bright blue to deep navy"></div>
    <div class="back-mark">
      <span class="back-mark__square"></span>
      <span class="back-mark__name">Verodex</span>
    </div>
  </section>
</body>
</html>
```